CREATE A BUSINESS CARD FOR A BOAT CLEANING SERVICE

WE ARE STARTING A NEW BOAT CLEANING BUSINESS. WE DIVE UNDERWATER TO CLEAN BOAT HULLS, JETTIES, UNDERWATER STRUCTURES ETC. WE ARE LOOKING FOR AN UPPERMARKET MODERN LOGO AND BUSINESS CARD AS ALOT OF OUR TARGET MARKET WILL BE HIGH END. YOU HAVE TO DESIGN A BUSINESS CARD AND LOGO SEPERATELY .
THE BUSINESS CARD DIMESNION MUST BE STANDARD SIZE.
The standard dimensions of a printed business card are 3.5 x 2 inches

Target Market(s)

UNDERWATER SERVICED

Industry/Entity Type

Business

Contact Information for Business Card

HOLLAND UNDERWATER SERVICES

Font styles to use
Serif

Colors

Designer to choose colors to be used in the design.

Requirements
Must have
• HOLLAND
Nice to have
• dark
Should not have
• more than 3 colors

```html
<!DOCTYPE html>
<html lang="en">
<head>
<meta charset="utf-8">
<title>Holland Underwater Services – Business Card</title>
<link href="https://fonts.googleapis.com/css2?family=Lato:wght@400;700&display=swap" rel="stylesheet">
<style>
  :root {
    --page: #d8d3cb;
    --card-white: #f7f8f9;
    --card-dark: #141517;
    --brand-blue: #2a7fd4;
    --text-light: #f1f2f3;
  }
  html, body {
    margin: 0;
    padding: 0;
    width: 1200px;
    height: 1023px;
    overflow: hidden;
    background: var(--page);
    font-family: "Lato", sans-serif;
  }
  .canvas {
    position: relative;
    width: 1200px;
    height: 1023px;
  }
  .card {
    position: absolute;
    left: 354px;
    top: 82px;
    width: 492px;
    height: 860px;
    border-radius: 26px;
    overflow: hidden;
    background: var(--card-white);
    box-shadow: 0 18px 40px rgba(0,0,0,0.28);
  }
  .card-shape {
    position: absolute;
    inset: 0;
  }
  .company-name {
    position: absolute;
    top: 160px;
    left: 60px;
    right: 60px;
    margin: 0;
    text-align: center;
    color: var(--brand-blue);
    font-size: 34px;
    font-weight: 400;
    line-height: 1.25;
  }
  .contact {
    position: absolute;
    left: 52px;
    top: 540px;
    color: var(--text-light);
  }
  .person-name {
    font-size: 30px;
    color: var(--brand-blue);
    letter-spacing: 2px;
    line-height: 1;
  }
  .person-role {
    font-size: 24px;
    margin-top: 6px;
  }
  .contact-list {
    list-style: none;
    margin: 20px 0 0 0;
    padding: 0;
    font-size: 19px;
  }
  .contact-list li {
    display: flex;
    align-items: center;
    height: 30px;
  }
  .contact-list svg {
    width: 14px;
    height: 14px;
    margin-right: 12px;
    fill: var(--brand-blue);
  }
  .accent { color: var(--brand-blue); }
  .address {
    margin-top: 14px;
    font-size: 19px;
    line-height: 27px;
  }
  .footer-name {
    position: absolute;
    left: 52px;
    bottom: 32px;
    display: flex;
    align-items: center;
    color: var(--text-light);
    font-size: 26px;
    font-weight: 700;
    letter-spacing: 1px;
  }
  .footer-dot {
    width: 28px;
    height: 28px;
    border-radius: 50%;
    background: var(--brand-blue);
    margin-right: 10px;
  }
  .partner-badge {
    position: absolute;
    right: 56px;
    bottom: 28px;
    width: 80px;
    height: 50px;
    border-radius: 50%;
    background: #1f5d8c;
  }
</style>
</head>
<body>
<main class="canvas">
  <section class="card" aria-label="Business card front">
    <svg class="card-shape" viewBox="0 0 492 860" aria-hidden="true">
      <path d="M0 338 L48 334 L272 518 L322 478 L492 478 L492 860 L0 860 Z" fill="#141517"/>
      <path d="M48 334 L492 404 L492 466 L318 466 L272 510 Z" fill="#2a7fd4" stroke="#ffffff" stroke-width="5" stroke-linejoin="round"/>
    </svg>

    <h1 class="company-name">HOLLAND UNDERWATER SERVICES</h1>

    <div class="contact">
      <div class="person-name">DAAN VERHOEF</div>
      <div class="person-role">CEO / Founder</div>
      <ul class="contact-list">
        <li><svg viewBox="0 0 16 16"><path d="M3 1 L6 1 L7 5 L5 6.5 C6 9 7 10 9.5 11 L11 9 L15 10 L15 13 C15 14 14 15 13 15 C6 15 1 10 1 3 C1 2 2 1 3 1 Z"/></svg>555-014-2270</li>
        <li><svg viewBox="0 0 16 16"><path d="M1 3 H15 V13 H1 Z M1 3 L8 9 L15 3" stroke="#141517" stroke-width="1.2"/></svg>info@hollandhullcare.com</li>
        <li><svg viewBox="0 0 16 16"><circle cx="8" cy="8" r="7"/></svg>www.<span class="accent">hollandhullcare</span>.com</li>
      </ul>
      <div class="address">Kadeweg 24 4811XY<br>Kaaphaven, Noordland</div>
    </div>

    <div class="footer-name"><span class="footer-dot"></span>HOLLAND</div>
    <div class="partner-badge" role="img" aria-label="Partner badge"></div>
  </section>
</main>
</body>
</html>
```